Residential Remodeling Contractor needs updated business card

I need a new design for my business card.
Name of the company is Ridgefell Construction. I need a card that commands presence, strength, integrity. I have been in business for 28 years. I am a Residential Remodeling Contractor that covers all aspects of a residential remodel and build.

```html
<!DOCTYPE html>
<html lang="en">
<head>
<meta charset="utf-8">
<title>Ridgefell Construction — Business Card</title>
<link href="https://fonts.googleapis.com/css2?family=Open+Sans:wght@400;700&display=swap" rel="stylesheet">
<style>
  :root {
    --backdrop: #222222;
    --card-blue: #213d7c;
    --card-edge: #172c5e;
    --card-shade: #162a5a;
    --ink-white: #ffffff;
    --ink-navy: #15285a;
  }
  * { box-sizing: border-box; margin: 0; padding: 0; }
  html, body {
    width: 1200px;
    height: 780px;
    overflow: hidden;
    background: var(--backdrop);
    font-family: "Open Sans", Arial, sans-serif;
  }
  .canvas {
    position: relative;
    width: 1200px;
    height: 780px;
    display: flex;
    align-items: center;
    justify-content: center;
    gap: 56px;
  }
  .card {
    position: relative;
    width: 525px;
    height: 300px;
    background: var(--card-blue);
    color: var(--ink-white);
    overflow: hidden;
    box-shadow:
      0 3px 0 var(--card-edge),
      0 6px 0 var(--card-shade),
      0 24px 40px rgba(0, 0, 0, 0.55);
  }

  /* Contact side */
  .card--contact .shade-band {
    position: absolute;
    inset: 0;
    background: linear-gradient(115deg,
      rgba(0, 0, 0, 0) 48%,
      rgba(15, 30, 70, 0.45) 58%,
      rgba(0, 0, 0, 0) 72%);
  }
  .holder {
    position: absolute;
    left: 128px;
    top: 52px;
    text-align: right;
  }
  .holder__name {
    font-size: 27px;
    font-weight: 700;
    line-height: 1.1;
    letter-spacing: 0.2px;
  }
  .holder__role {
    font-size: 15px;
    font-weight: 400;
    margin-top: 2px;
  }
  .address {
    position: absolute;
    left: 40px;
    bottom: 44px;
    font-size: 15px;
    font-weight: 400;
  }
  .contact-list {
    position: absolute;
    left: 292px;
    top: 118px;
    list-style: none;
    font-size: 15.5px;
    line-height: 1.45;
  }
  .contact-list li {
    display: flex;
    align-items: center;
    gap: 7px;
  }
  .contact-list svg {
    width: 14px;
    height: 14px;
    flex: none;
  }

  /* Brand side */
  .card--brand {
    display: flex;
    align-items: center;
    justify-content: center;
  }
  .brand {
    display: flex;
    align-items: center;
    gap: 16px;
    color: var(--ink-navy);
    font-weight: 700;
  }
  .brand__dot {
    width: 18px;
    height: 18px;
    border-radius: 50%;
    background: var(--ink-navy);
  }
  .brand__name {
    font-size: 34px;
    line-height: 1.05;
    letter-spacing: 1px;
    text-transform: uppercase;
  }
</style>
</head>
<body>
<main class="canvas">

  <section class="card card--contact" aria-label="Contact side of business card">
    <div class="shade-band"></div>

    <div class="holder">
      <p class="holder__name">Marta Kovalenko</p>
      <p class="holder__role">Managing Director</p>
    </div>

    <ul class="contact-list">
      <li>
        <svg viewBox="0 0 24 24" aria-hidden="true"><path fill="#fff" d="M6.6 10.8a15.1 15.1 0 0 0 6.6 6.6l2.2-2.2a1 1 0 0 1 1-.25 11.4 11.4 0 0 0 3.6.57 1 1 0 0 1 1 1V20a1 1 0 0 1-1 1A17 17 0 0 1 3 4a1 1 0 0 1 1-1h3.5a1 1 0 0 1 1 1c0 1.25.2 2.45.57 3.57a1 1 0 0 1-.25 1z"/></svg>
        <span>(555) 204-7316</span>
      </li>
      <li>
        <svg viewBox="0 0 24 24" aria-hidden="true"><rect x="2" y="5" width="20" height="14" rx="1.5" fill="#fff"/><path d="M3 6.5l9 6.5 9-6.5" fill="none" stroke="#213d7c" stroke-width="1.8"/></svg>
        <span>info@ridgefellbuild.com</span>
      </li>
      <li>
        <svg viewBox="0 0 24 24" aria-hidden="true"><circle cx="12" cy="12" r="10" fill="#fff"/><path d="M2 12h20M12 2c3 3 3 17 0 20M12 2c-3 3-3 17 0 20" fill="none" stroke="#213d7c" stroke-width="1.4"/></svg>
        <span>www.ridgefellbuild.com</span>
      </li>
    </ul>

    <p class="address">4170 Alder Bend Dr. Suite 310 Granbury, TX 76048</p>
  </section>

  <section class="card card--brand" aria-label="Brand side of business card">
    <div class="brand">
      <span class="brand__dot" aria-hidden="true"></span>
      <p class="brand__name">Ridgefell<br>Construction</p>
    </div>
  </section>

</main>
</body>
</html>
```